Header/Banner Design for Website

Looking for a banner/header design for www.nestfixerdiaries.net Should be fun and whimsical, and include the name of the website, something to do with home improvement or tools, and a caricature of a young, beautiful 20 something blond who the website revolves around. The website is about a young woman who bought her first house and it taking on all of the renovations and remodeling on her own for the first time.

The header/banner should include the same colors that are in the website. The width should be no more than 430 pixels, the height is flexible but the current space in the header is 85 pixels...looking for some creativity. any questions, please ask. Attached an image that she liked for the image of the woman (would like to see versions of this included)
Updates

Target Market(s)

women 20+ that are new home owners or that are tackling home improvement on their own

Industry/Entity Type

Home Improvement

Requirements
Must have
• color coordinate with the website
should feature a young, blond, female caricature
should include the name of the website

```html
<!DOCTYPE html>
<html lang="en">
<head>
<meta charset="utf-8">
<title>Nest Fixer Diaries – Header Banners</title>
<link rel="stylesheet" href="https://fonts.googleapis.com/css2?family=Teko:wght@500&family=Arimo:wght@400;700&display=swap">
<style>
  :root {
    --canvas: #c0c0c0;
    --brand-pink: #f7359a;
    --white: #ffffff;
    --field-pink: #fde4f5;
    --button-plum: #8a1a59;
    --ink: #111111;
    --photo-light: #f4efe9;
    --photo-hair: #e2c07a;
    --photo-skin: #e9b48f;
    --photo-shirt: #2f78c4;
  }
  * { box-sizing: border-box; margin: 0; padding: 0; }
  html, body {
    width: 1200px;
    height: 365px;
    overflow: hidden;
    background: var(--canvas);
  }
  .canvas { position: relative; width: 1200px; height: 365px; }

  .banner {
    position: absolute;
    height: 125px;
    background: var(--brand-pink);
    overflow: hidden;
  }
  .banner--compact { left: 378px; top: 55px; width: 445px; }
  .banner--wide { left: 77px; top: 211px; width: 1047px; }

  .banner__photo {
    position: absolute;
    left: 0; top: 0;
    height: 100%;
    background:
      radial-gradient(ellipse 38% 42% at 42% 30%, var(--photo-skin) 0%, transparent 70%),
      radial-gradient(ellipse 45% 55% at 38% 18%, var(--photo-hair) 0%, transparent 75%),
      radial-gradient(ellipse 40% 35% at 30% 85%, var(--photo-shirt) 0%, transparent 75%),
      linear-gradient(90deg, var(--photo-light) 0%, var(--photo-light) 85%, var(--brand-pink) 100%);
  }
  .banner--compact .banner__photo { width: 180px; }
  .banner--wide .banner__photo { width: 188px; }

  .site-name {
    position: absolute;
    font-family: "Teko", sans-serif;
    font-weight: 500;
    color: var(--white);
    text-transform: uppercase;
    line-height: 1;
    white-space: nowrap;
  }
  .site-name__lead { display: block; }
  .site-name__tail { display: block; }

  .banner--compact .site-name { left: 190px; top: 20px; }
  .banner--compact .site-name__lead { font-size: 64px; height: 50px; }
  .banner--compact .site-name__tail { font-size: 30px; margin-left: 50px; }

  .banner--wide .site-name { left: 202px; top: 22px; display: flex; align-items: flex-end; }
  .banner--wide .site-name__lead { font-size: 86px; height: 72px; }
  .banner--wide .site-name__tail { font-size: 38px; margin-left: 18px; height: 32px; }

  .search {
    position: absolute;
    left: 693px;
    top: 43px;
    display: flex;
    align-items: center;
  }
  .search__field {
    width: 211px;
    height: 38px;
    background: var(--field-pink);
    border: 2px solid var(--white);
    font-family: "Arimo", sans-serif;
    font-size: 13px;
    color: var(--ink);
    padding: 0 6px;
    display: flex;
    align-items: center;
  }
  .search__button {
    width: 118px;
    height: 42px;
    background: var(--button-plum);
    border-radius: 2px;
    color: var(--white);
    font-family: "Arimo", sans-serif;
    font-weight: 700;
    font-size: 17px;
    display: flex;
    align-items: center;
    justify-content: center;
    gap: 6px;
  }
</style>
</head>
<body>
<main class="canvas">

  <header class="banner banner--compact">
    <div class="banner__photo" role="img" aria-label="Photo of a smiling young blond woman in a cap giving a thumbs up while holding paint rollers and brushes"></div>
    <div class="site-name">
      <span class="site-name__lead">Nest</span>
      <span class="site-name__tail">Fixer Diaries</span>
    </div>
  </header>

  <header class="banner banner--wide">
    <div class="banner__photo" role="img" aria-label="Photo of a smiling young blond woman in a cap giving a thumbs up while holding paint rollers and brushes"></div>
    <div class="site-name">
      <span class="site-name__lead">Nest</span>
      <span class="site-name__tail">Fixer Diaries</span>
    </div>
    <form class="search" role="search">
      <div class="search__field">Search</div>
      <div class="search__button">
        Search
        <svg width="18" height="18" viewBox="0 0 18 18" aria-hidden="true">
          <circle cx="7" cy="7" r="5" fill="#cfe9ff" stroke="#ffffff" stroke-width="2"/>
          <line x1="10.5" y1="10.5" x2="16" y2="16" stroke="#ffffff" stroke-width="3" stroke-linecap="round"/>
        </svg>
      </div>
    </form>
  </header>

</main>
</body>
</html>
```